Business card design for my company.
I would like the card's background colour to be black. You can also see our web site to get an idea of our brand. https://www.tmwhomecrafting.com.au/
- Name
- Email

```html
<!DOCTYPE html>
<html lang="en">
<head>
<meta charset="utf-8">
<title>TMW Home Crafting – Business Card</title>
<link rel="stylesheet" href="https://fonts.googleapis.com/css2?family=Roboto:wght@400;500;700&display=swap">
<style>
  :root {
    --backdrop: #2a2a2a;
    --card-black: #1f1f20;
    --card-black-light: #2a2a2b;
    --brand-green: #0e9a3f;
    --text-white: #ffffff;
    --text-soft: #e6e6e6;
    --emboss: #3a3a3b;
  }
  * { margin: 0; padding: 0; box-sizing: border-box; }
  html, body {
    width: 1200px; height: 852px; overflow: hidden;
    background: var(--backdrop);
    font-family: "Roboto", Arial, sans-serif;
  }
  .stage { position: relative; width: 1200px; height: 852px; }
  .card {
    position: absolute; top: 283px;
    width: 500px; height: 286px; border-radius: 22px; overflow: hidden;
    background: linear-gradient(160deg, var(--card-black-light), var(--card-black));
    box-shadow: 0 6px 0 var(--brand-green);
  }
  .card--front { left: 70px; }
  .card--back { left: 630px; }

  .front-mark {
    position: absolute; left: 0; right: 0; top: 98px;
    display: flex; align-items: center; justify-content: center; gap: 12px;
  }
  .front-mark__square { width: 22px; height: 22px; background: var(--emboss); }
  .front-mark__name {
    font-weight: 700; font-size: 30px; letter-spacing: 1px; color: var(--emboss);
  }
  .front-web {
    position: absolute; right: 34px; bottom: 28px;
    font-size: 13px; color: var(--text-soft);
  }

  .back-art { position: absolute; inset: 0; }
  .back-mark {
    position: absolute; left: 34px; top: 196px;
    display: flex; align-items: center; gap: 10px;
  }
  .back-mark__square { width: 18px; height: 18px; background: var(--brand-green); }
  .back-mark__name {
    font-weight: 700; font-size: 21px; letter-spacing: 0.5px; color: var(--text-white);
  }
  .contact {
    position: absolute; right: 26px; top: 30px; list-style: none;
    text-align: right; font-size: 12.5px; line-height: 18px; color: var(--text-soft);
  }
  .contact li { display: flex; justify-content: flex-end; align-items: center; gap: 8px; }
  .contact svg { width: 11px; height: 11px; fill: var(--brand-green); }
  .holder {
    position: absolute; right: 36px; top: 196px; text-align: right; color: var(--text-white);
  }
  .holder__name { font-weight: 700; font-size: 20px; }
  .holder__role { font-size: 12px; margin-top: 2px; }
</style>
</head>
<body>
<main class="stage">
  <section class="card card--front" aria-label="Card front">
    <div class="front-mark">
      <span class="front-mark__square"></span>
      <span class="front-mark__name">TMW Home Crafting</span>
    </div>
    <p class="front-web">www.tmwhomecrafting.com.au</p>
  </section>

  <section class="card card--back" aria-label="Card back">
    <svg class="back-art" viewBox="0 0 500 286" aria-hidden="true">
      <polygon points="205,286 380,168 500,168 500,286" fill="var(--brand-green)"/>
      <polygon points="178,286 362,160 375,160 191,286" fill="var(--brand-green)"/>
    </svg>

    <div class="back-mark">
      <span class="back-mark__square"></span>
      <span class="back-mark__name">TMW Home Crafting</span>
    </div>

    <ul class="contact">
      <li>0400 123 456
        <svg viewBox="0 0 24 24"><path d="M6.6 10.8a15 15 0 0 0 6.6 6.6l2.2-2.2c.3-.3.7-.4 1-.2 1.1.4 2.3.6 3.6.6.6 0 1 .4 1 1V20c0 .6-.4 1-1 1A17 17 0 0 1 3 4c0-.6.4-1 1-1h3.5c.6 0 1 .4 1 1 0 1.3.2 2.5.6 3.6.1.3 0 .7-.2 1z"/></svg></li>
      <li>info@tmwhomecrafting.com.au
        <svg viewBox="0 0 24 24"><path d="M2 5h20v14H2zM4 7v.5l8 5 8-5V7l-8 5z"/></svg></li>
      <li>www.tmwhomecrafting.com.au
        <svg viewBox="0 0 24 24"><path d="M12 2a10 10 0 1 0 0 20 10 10 0 0 0 0-20zm0 2c1 1.3 1.8 3 2.1 5H9.9C10.2 7 11 5.3 12 4zM4.3 11h4.5c0 .7 0 1.3.1 2H4.3a8 8 0 0 1 0-2zm5.6 4h4.2c-.3 2-1.1 3.7-2.1 5-1-1.3-1.8-3-2.1-5zm5.3-4h4.5a8 8 0 0 1 0 2h-4.6c.1-.7.1-1.3.1-2z"/></svg></li>
      <li>Riverbend, Tasmania, Australia
        <svg viewBox="0 0 24 24"><path d="M12 2a7 7 0 0 0-7 7c0 5 7 13 7 13s7-8 7-13a7 7 0 0 0-7-7zm0 9.5a2.5 2.5 0 1 1 0-5 2.5 2.5 0 0 1 0 5z"/></svg></li>
    </ul>

    <div class="holder">
      <p class="holder__name">Liam Harcourt</p>
      <p class="holder__role">General Manager</p>
    </div>
  </section>
</main>
</body>
</html>
```